Velora Reggaeton Night

I'd like to create a flyer / poster for a reaggaeton Xmas party in London. The party will be titled "Velora" and will be VIP for friends of friends only. The concept has to remain classy and stylish as I don't want it to be related to anything tropical at first glance. People attending the party will be a bit up-scale so the style is key. I am thinking of a black background and golden or silver letters, which give a bit of a "bling" look. Since the party will take place in Central London, I was thinking perhaps including something that relates to the city (St. Wendel's Cathedral, the Quillon, etc.). I have seen a few ideas and I am happy to send those over to illustrate a bit better what I am thinking of. Color wise, the theme could be very black and grey (for the London buildings) and only keep a few bright red colors if including London double decker buses or phone booths. Need to include something that gives the poster / flyer a Latin vibe as well.

Target Market(s)

25-35 year olds. Young professionals living in London. Latin American and European origins. People that enjoy dancing and like reggaeton music in particular.

Industry/Entity Type

Latin American Café

Requirements
Must have
• Must have the name of the party, VELORA, as a big part of the flyer. Also the words "reggaeton party" or "reggaeton night". Something catchy. The date will be December 16 2017. Time will be 7pm to 3am. Location is Central London (Bank). I don't want to specify the location as I want it to be "secret" and only people with the ticket will be given the address.
Nice to have
• Nice to have something that resembles London but also the Latin, bling vibe of reggaeton music. Velora means "flirt" in Spanish so I want the design to be flirty but elegant and very stylish. VELORA could be written in Gold or Silver to make it stand-out. Could be made up of yellow light bulbs as well. And could include a rose to make it more flirty. See examples attached.
Should not have
• Typical tropical or Cuban type designs. I don't want anything too colorful as I want to keep it classy and stylish. Try to avoid people dancing in the flyer. Don't want a photo of sexy women in the flyer. Need to keep it classy.

```html
<!DOCTYPE html>
<html lang="en">
<head>
<meta charset="utf-8">
<title>Velora Reggaeton Night</title>
<link rel="stylesheet" href="https://fonts.googleapis.com/css2?family=Montserrat:wght@800&family=Oswald:wght@400;500&family=Great+Vibes&display=swap">
<style>
  :root {
    --page: #f4f4f4;
    --ink: #000000;
    --gold-light: #fbe6a6;
    --gold: #d9a441;
    --gold-deep: #8a5a14;
    --silver-light: #ffffff;
    --silver: #c9c4bf;
    --silver-deep: #8d877f;
    --green-bright: #8bc43c;
    --green-mid: #3f8a2c;
    --green-dark: #143a1c;
    --amber: #6b3a06;
    --smoke: #262a27;
    --caption: #d8d8d8;
  }
  html, body {
    margin: 0;
    width: 1200px;
    height: 1200px;
    overflow: hidden;
    background: var(--page);
  }
  .canvas {
    position: relative;
    width: 1200px;
    height: 1200px;
  }
  .poster {
    position: absolute;
    left: 222px;
    top: 40px;
    width: 756px;
    height: 1120px;
    display: block;
  }
  .title { font-family: "Montserrat", sans-serif; font-weight: 800; }
  .script { font-family: "Great Vibes", cursive; }
  .hours { font-family: "Oswald", sans-serif; font-weight: 500; }
  .date { font-family: "Montserrat", sans-serif; font-weight: 800; }
  .place { font-family: "Oswald", sans-serif; font-weight: 400; letter-spacing: 6px; }
</style>
</head>
<body>
<div class="canvas">
  <svg class="poster" viewBox="0 0 920 1365" xmlns="http://www.w3.org/2000/svg">
    <defs>
      <radialGradient id="glow" cx="0.62" cy="0.3" r="0.6">
        <stop offset="0" stop-color="#f2e23a" stop-opacity="0.95"/>
        <stop offset="0.45" stop-color="#b06a10" stop-opacity="0.7"/>
        <stop offset="1" stop-color="#000" stop-opacity="0"/>
      </radialGradient>
      <linearGradient id="greenFace" x1="0" y1="0" x2="0" y2="1">
        <stop offset="0" stop-color="var(--green-bright)"/>
        <stop offset="1" stop-color="var(--green-mid)"/>
      </linearGradient>
      <linearGradient id="silverText" x1="0" y1="0" x2="0" y2="1">
        <stop offset="0" stop-color="var(--silver-light)"/>
        <stop offset="0.55" stop-color="var(--silver)"/>
        <stop offset="1" stop-color="var(--silver-deep)"/>
      </linearGradient>
      <linearGradient id="goldText" x1="0" y1="0" x2="0" y2="1">
        <stop offset="0" stop-color="var(--gold-light)"/>
        <stop offset="0.5" stop-color="var(--gold)"/>
        <stop offset="1" stop-color="var(--gold-deep)"/>
      </linearGradient>
      <linearGradient id="goldRule" x1="0" y1="0" x2="1" y2="0">
        <stop offset="0" stop-color="var(--gold)" stop-opacity="0"/>
        <stop offset="0.5" stop-color="var(--gold)"/>
        <stop offset="1" stop-color="var(--gold)" stop-opacity="0"/>
      </linearGradient>
    </defs>

    <!-- ground -->
    <rect class="poster-ground" width="920" height="1365" fill="var(--ink)"/>

    <!-- background prisms -->
    <g class="bg-prisms" opacity="0.45">
      <polygon points="20,20 300,20 160,420" fill="var(--amber)"/>
      <polygon points="600,20 900,20 900,520" fill="var(--amber)"/>
      <polygon points="0,200 260,660 0,660" fill="#3a1f04"/>
      <polygon points="920,260 680,700 920,700" fill="#3a1f04"/>
    </g>

    <!-- fireworks burst area -->
    <rect class="fireworks" x="40" y="20" width="860" height="660" fill="url(#glow)" role="img" aria-label="Golden fireworks bursting behind the prism stack"/>

    <!-- prism stack -->
    <g class="prism-stack">
      <polygon points="460,120 720,690 200,690" fill="url(#greenFace)" opacity="0.85"/>
      <polygon points="460,120 610,380 310,380" fill="var(--green-dark)"/>
      <polygon points="460,245 535,380 385,380" fill="var(--green-bright)"/>
      <polygon points="318,420 602,420 648,500 272,500" fill="var(--ink)"/>
      <polygon points="275,500 650,500 460,690" fill="#1f5a2a"/>
      <polygon points="460,610 540,690 380,690" fill="#c8d93a"/>
      <polygon points="460,760 800,975 125,975" fill="var(--smoke)"/>
    </g>

    <!-- city skyline -->
    <rect class="skyline skyline-left" x="15" y="580" width="170" height="240" fill="#c8965a" opacity="0.28" role="img" aria-label="Gold line drawing of the London skyline with the big wheel"/>
    <rect class="skyline skyline-right" x="680" y="520" width="225" height="300" fill="#c8965a" opacity="0.28" role="img" aria-label="Gold line drawing of a clock tower and a rounded glass tower"/>

    <!-- title plate -->
    <g class="title-plate">
      <rect x="170" y="697" width="575" height="128" rx="8" fill="#0b0906" stroke="var(--gold)" stroke-width="3"/>
      <text class="title" x="457" y="795" font-size="98" text-anchor="middle" fill="url(#silverText)">VELORA</text>
    </g>

    <!-- event subtitle -->
    <g class="subtitle" fill="url(#goldText)">
      <text class="script" x="205" y="975" font-size="118" transform="rotate(-20 205 975)">Reggaeton</text>
      <text class="script" x="420" y="1005" font-size="128" transform="rotate(-20 420 1005)">Night</text>
    </g>

    <!-- details -->
    <g class="details">
      <rect x="15" y="1034" width="890" height="2" fill="url(#goldRule)"/>
      <text class="hours" x="460" y="1102" font-size="58" text-anchor="middle" fill="url(#goldText)">7PM - 3AM</text>
      <rect x="15" y="1120" width="890" height="2" fill="url(#goldRule)"/>
      <text class="date" x="460" y="1205" font-size="70" text-anchor="middle" fill="url(#silverText)">16.12.2017</text>
      <rect x="15" y="1232" width="890" height="2" fill="url(#goldRule)"/>
      <text class="place" x="460" y="1273" font-size="23" text-anchor="middle" fill="var(--caption)">CENTRAL LONDON</text>
    </g>
  </svg>
</div>
</body>
</html>
```